Larkspur Cosmetics Website needs a professional upgrade

I need a new design for an online cosmetics store that looks professional and clean but also has a natural look and feel to it.

The women in the top bar (Image attached) needs to be included and she is on all of our advertising banners/ stands though I would like to come away from the black.

Design Needs:
- 1 x Home Page
- 1 x Products Page

I have plenty more website coming along so hopefully can find someone who I can rely on for a quick turnover :)

Happy designing !

Industry/Entity Type

Store

Number of Pages Required

2 page

Font styles to use
Sans Serif

Requirements
Must have
• - Natural Clean look
Should not have
• - The current black and green colours

```html
<!DOCTYPE html>
<html lang="en">
<head>
<meta charset="utf-8">
<title>Larkspur Cosmetics — Home</title>
<link href="https://fonts.googleapis.com/css2?family=Open+Sans:wght@400;600;700&display=swap" rel="stylesheet">
<style>
:root{
  --coral:#e0675f;
  --coral-light:#ec8a83;
  --top:#1e1e1e;
  --bar:#353535;
  --panel:#2f2f2f;
  --ink:#222;
  --muted:#555;
  --line:#d6d6d6;
  --star:#f5a623;
  --footer:#2b2b2b;
  --footer-base:#1c1c1c;
  --white:#fff;
}
*{box-sizing:border-box;margin:0;padding:0}
html,body{width:882px;height:1200px;overflow:hidden}
body{font-family:"Open Sans",sans-serif;background:var(--white);color:var(--ink);position:relative}
.abs{position:absolute}
.topbar{left:0;top:0;width:882px;height:30px;background:var(--top);color:#ddd;font-size:10px}
.topbar span{position:absolute;top:8px;display:flex;align-items:center;gap:5px}
.header{left:0;top:30px;width:882px;height:41px;background:var(--bar)}
.nav{left:0;top:71px;width:882px;height:47px;background:var(--coral)}
.nav ul{list-style:none;position:absolute;left:324px;top:0;display:flex;height:47px}
.nav li{color:#fff;font-size:9.5px;display:flex;align-items:center;padding:0 14px;border-left:1px solid rgba(255,255,255,.25);height:47px}
.nav li.active{background:var(--coral-light)}
.logo{left:67px;top:30px;width:128px;height:88px;background:#141414;color:#fff;text-align:center;display:flex;flex-direction:column;align-items:center;justify-content:center;gap:6px}
.logo .dot{width:26px;height:26px;border-radius:50%;border:2px solid #c9a86a}
.logo .name{font-size:11px;font-weight:600;letter-spacing:.5px}
.search{left:404px;top:41px;display:flex;height:19px}
.search .cat{width:88px;background:#4a4a4a;border-radius:10px 0 0 10px;color:#fff;font-size:8px;font-weight:700;display:flex;align-items:center;justify-content:center}
.search .field{width:220px;background:#4a4a4a;margin-left:2px;color:#aaa;font-size:6.5px;display:flex;align-items:center;padding-left:14px}
.search .go{width:36px;background:#4a4a4a;margin-left:2px;border-radius:0 10px 10px 0;display:flex;align-items:center;justify-content:center}
.cart{left:777px;top:30px;width:43px;height:41px;background:#4a4a4a;color:#fff;font-size:7.5px;display:flex;flex-direction:column;align-items:center;justify-content:center;gap:2px}
.hero{left:67px;top:118px;width:756px;height:171px;background:linear-gradient(90deg,#c7d9b4 0%,#e6eedc 45%,#e9dcd4 62%,#b9cf93 80%,#8faa5f 100%)}
.hero h1{position:absolute;left:90px;top:48px;font-weight:400;font-size:22px;line-height:25px;color:#4a4a3a;text-align:center}
.cathead{left:67px;top:326px;width:172px;height:33px;background:var(--panel);border-bottom:3px solid var(--coral);color:#fff;font-size:10px;font-weight:700;letter-spacing:1px;display:flex;align-items:center;padding-left:12px;gap:12px}
.catlist{left:67px;top:359px;width:172px;height:213px;border:1px solid #e4e4e4;border-top:none;list-style:none}
.catlist li{height:35.4px;font-size:7.8px;display:flex;align-items:center;justify-content:space-between;padding:0 8px 0 13px;color:#333}
.catlist li b{font-weight:400;font-size:13px;color:#444}
.newhead{left:67px;top:592px;width:172px;height:36px;background:var(--panel);color:#fff;font-size:8px;font-weight:700;padding:12px 10px}
.newhead .arrows{position:absolute;right:0;bottom:0;width:52px;height:20px;background:var(--coral);clip-path:polygon(18% 0,100% 0,100% 100%,0 100%);color:#fff;font-size:10px;display:flex;justify-content:flex-end;gap:14px;padding-right:6px;align-items:center}
.mini{left:67px;width:172px;height:54px}
.mini .thumb{position:absolute;left:0;top:0;width:54px;height:54px;border:1px solid #e6e6e6}
.mini .thumb i{position:absolute;inset:10px;border-radius:4px}
.mini .t{position:absolute;left:67px;top:7px;font-size:8px}
.mini .p{position:absolute;left:67px;top:27px;font-size:8px;font-weight:700}
.title{left:259px;top:324px;font-size:21px;font-weight:700;color:#333;letter-spacing:-.2px}
.pager{left:741px;top:325px;width:72px;height:28px;background:#111;color:#fff;display:flex;align-items:center;justify-content:space-between;padding:0 9px;font-size:14px}
.pager .slash{width:12px;height:28px;background:#fff;transform:skewX(-25deg)}
.card{width:175px;height:254px;border:1px solid #bdbdbd;background:#fff}
.card .n{position:absolute;left:11px;top:10px;font-size:7.5px;color:#222}
.card .pr{position:absolute;left:11px;top:27px;font-size:12px;font-weight:600}
.card .stars{position:absolute;left:11px;top:48px}
.card .badge{position:absolute;right:-1px;top:38px;width:40px;height:20px;background:var(--coral);color:#fff;font-size:7.5px;display:flex;align-items:center;justify-content:center;padding-left:6px;clip-path:polygon(18% 0,100% 0,100% 100%,18% 100%,0 50%)}
.card .shot{position:absolute;left:38px;top:85px;width:100px;height:135px;border-radius:6px}
.footer{left:0;top:944px;width:882px;height:210px;background:var(--footer);color:#e6e6e6}
.col{position:absolute;top:44px}
.col h3{font-size:9.5px;font-weight:600;letter-spacing:.3px;color:#fff}
.col h3::after{content:"";display:block;width:42px;height:2px;background:#fff;margin-top:9px}
.col ul{list-style:none;margin-top:15px}
.col li{font-size:9.5px;height:23.4px}
.col li.hl{color:var(--coral)}
.social{position:absolute;left:679px;top:163px;display:flex;gap:14px}
.social i{width:12px;height:12px;border-radius:50%;background:#e6e6e6;display:block}
.social i:first-child{background:var(--coral)}
.base{left:0;top:1154px;width:882px;height:46px;background:var(--footer-base);color:#fff;font-size:9.5px}
.base .c{position:absolute;left:70px;top:16px}
.pay{position:absolute;right:58px;top:16px;display:flex;gap:6px}
.pay i{display:block;width:24px;height:14px;border-radius:3px}
</style>
</head>
<body>
<svg width="0" height="0" style="position:absolute">
  <defs>
    <symbol id="star-on" viewBox="0 0 12 12"><rect width="12" height="12" fill="#fbe3b0" stroke="#e5c07a" stroke-width=".6"/><polygon points="6,1.5 7.3,4.5 10.5,4.7 8,6.8 8.8,10 6,8.3 3.2,10 4,6.8 1.5,4.7 4.7,4.5" fill="#f5a623"/></symbol>
    <symbol id="star-off" viewBox="0 0 12 12"><rect width="12" height="12" fill="#f1f1f1" stroke="#ddd" stroke-width=".6"/><polygon points="6,1.5 7.3,4.5 10.5,4.7 8,6.8 8.8,10 6,8.3 3.2,10 4,6.8 1.5,4.7 4.7,4.5" fill="#fff"/></symbol>
  </defs>
</svg>

<div class="abs topbar">
  <span style="left:70px"><svg width="9" height="9" viewBox="0 0 10 10"><path d="M2 1l2 2-1 1.3c.6 1.2 1.5 2.1 2.7 2.7L7 6l2 2-1.3 1.4C4.5 9 1 5.5.6 2.3z" fill="#ddd"/></svg>Call us now : + 123 555 0190</span>
  <span style="left:234px"><svg width="10" height="8" viewBox="0 0 10 8"><rect width="10" height="8" fill="#ddd"/><path d="M0 0l5 4 5-4" stroke="#1e1e1e" fill="none"/></svg>Email : hello@larkspurshop.com</span>
  <span style="left:633px">English ˅</span>
  <span style="left:685px">Currency : USD ˅</span>
  <span style="left:772px">Account ˅</span>
</div>

<div class="abs header"></div>
<div class="abs search">
  <div class="cat">Categories ˅</div>
  <div class="field">Enter your search key word....</div>
  <div class="go"><svg width="12" height="12" viewBox="0 0 12 12"><circle cx="5" cy="5" r="3.8" stroke="#fff" stroke-width="1.5" fill="none"/><path d="M8 8l3.3 3.3" stroke="#fff" stroke-width="1.6"/></svg></div>
</div>
<div class="abs cart">
  <svg width="16" height="13" viewBox="0 0 16 13"><path d="M0 1h3l2 8h8l2-6H4" stroke="#fff" stroke-width="1.4" fill="none"/><circle cx="6" cy="11.5" r="1.2" fill="#fff"/><circle cx="12" cy="11.5" r="1.2" fill="#fff"/></svg>
  0 ITEM
</div>

<nav class="abs nav">
  <ul>
    <li class="active">HOME</li><li>ABOUT</li><li>PRODUCTS</li><li>TREATMENTS</li><li>MEDIA</li><li>STORIES</li><li>CONTACT US</li>
  </ul>
</nav>

<div class="abs logo">
  <div class="dot"></div>
  <div class="name">LARKSPUR</div>
</div>

<div class="abs hero" role="img" aria-label="Campaign banner: woman with glowing skin among green leaves beside a range of skincare boxes and jars">
  <h1>Nature's Most<br>Potent Ingredients from<br>around the World</h1>
</div>

<div class="abs cathead">
  <svg width="12" height="10" viewBox="0 0 12 10"><g fill="#fff"><rect width="2" height="2"/><rect y="4" width="2" height="2"/><rect y="8" width="2" height="2"/><rect x="3" width="9" height="2"/><rect x="3" y="4" width="9" height="2"/><rect x="3" y="8" width="9" height="2"/></g></svg>
  CATEGORIES
</div>
<ul class="abs catlist">
  <li>WOMEN'S <b>+</b></li><li>MEN'S <b>+</b></li><li>FOOTWEAR <b>+</b></li><li>JEWELERY</li><li>ACCESSORIES</li><li>KIDS</li>
</ul>

<div class="abs newhead">NEW PRODUCTS<div class="arrows">‹ <span>›</span></div></div>
<div class="abs mini" style="top:638px"><div class="thumb" role="img" aria-label="Laptop"><i style="background:linear-gradient(#e2e2e2,#b8b8b8);inset:20px 8px"></i></div><div class="t">Laptop</div><div class="p">$26.00</div></div>
<div class="abs mini" style="top:711px"><div class="thumb" role="img" aria-label="Yellow handbag"><i style="background:#c9c43a"></i></div><div class="t">Hand BAg</div><div class="p">$26.00</div></div>
<div class="abs mini" style="top:784px"><div class="thumb" role="img" aria-label="Flower bouquet"><i style="background:linear-gradient(#b7a0d8,#8aa06a)"></i></div><div class="t">Flower Bucket</div><div class="p">$26.00</div></div>
<div class="abs mini" style="top:858px"><div class="thumb" role="img" aria-label="Yellow mobile phone"><i style="background:#e9e23a"></i></div><div class="t">Mobile</div><div class="p">$26.00</div></div>

<h2 class="abs title">MOSTVIEWED PRODUCTS</h2>
<div class="abs pager">‹<span class="slash"></span>›</div>

<div class="abs card" style="left:258px;top:380px">
  <div class="n">SMALL BAGS</div><div class="pr">$50.56</div>
  <svg class="stars" width="70" height="12"><use href="#star-on" x="0" width="12" height="12"/><use href="#star-on" x="14" width="12" height="12"/><use href="#star-on" x="28" width="12" height="12"/><use href="#star-off" x="42" width="12" height="12"/><use href="#star-off" x="56" width="12" height="12"/></svg>
  <div class="shot" role="img" aria-label="Cleansing tube with green box" style="background:linear-gradient(90deg,#eeeeee 45%,#8ea23a 55%)"></div>
</div>
<div class="abs card" style="left:447px;top:380px">
  <div class="n">SHOE</div><div class="pr">$28.45</div>
  <svg class="stars" width="70" height="12"><use href="#star-on" x="0" width="12" height="12"/><use href="#star-on" x="14" width="12" height="12"/><use href="#star-on" x="28" width="12" height="12"/><use href="#star-off" x="42" width="12" height="12"/><use href="#star-off" x="56" width="12" height="12"/></svg>
  <div class="badge">NEW</div>
  <div class="shot" role="img" aria-label="Serum bottle with gold box" style="background:linear-gradient(90deg,#e4e4e4 45%,#6f5a2c 55%)"></div>
</div>
<div class="abs card" style="left:639px;top:380px">
  <div class="n">STYLISH PURSE</div><div class="pr">$65.23</div>
  <svg class="stars" width="70" height="12"><use href="#star-on" x="0" width="12" height="12"/><use href="#star-on" x="14" width="12" height="12"/><use href="#star-on" x="28" width="12" height="12"/><use href="#star-off" x="42" width="12" height="12"/><use href="#star-off" x="56" width="12" height="12"/></svg>
  <div class="shot" role="img" aria-label="Purple skincare set with jar and tube" style="background:linear-gradient(135deg,#3a3a3a,#9a3e9e 55%,#e6e6e6)"></div>
</div>

<div class="abs card" style="left:256px;top:648px">
  <div class="n">SMALL BAGS</div><div class="pr">$50.56</div>
  <svg class="stars" width="70" height="12"><use href="#star-on" x="0" width="12" height="12"/><use href="#star-on" x="14" width="12" height="12"/><use href="#star-on" x="28" width="12" height="12"/><use href="#star-off" x="42" width="12" height="12"/><use href="#star-off" x="56" width="12" height="12"/></svg>
  <div class="badge">NEW</div>
  <div class="shot" role="img" aria-label="Serum bottle with gold box" style="background:linear-gradient(90deg,#e4e4e4 45%,#6f5a2c 55%)"></div>
</div>
<div class="abs card" style="left:447px;top:648px">
  <div class="n">SHOE</div><div class="pr">$28.45</div>
  <svg class="stars" width="70" height="12"><use href="#star-on" x="0" width="12" height="12"/><use href="#star-on" x="14" width="12" height="12"/><use href="#star-on" x="28" width="12" height="12"/><use href="#star-off" x="42" width="12" height="12"/><use href="#star-off" x="56" width="12" height="12"/></svg>
  <div class="shot" role="img" aria-label="Three green product boxes" style="background:linear-gradient(90deg,#8ea23a,#6e8028);top:95px;height:110px;width:110px;left:33px"></div>
</div>
<div class="abs card" style="left:638px;top:648px">
  <div class="n">STYLISH PURSE</div><div class="pr">$65.23</div>
  <svg class="stars" width="70" height="12"><use href="#star-on" x="0" width="12" height="12"/><use href="#star-on" x="14" width="12" height="12"/><use href="#star-on" x="28" width="12" height="12"/><use href="#star-off" x="42" width="12" height="12"/><use href="#star-off" x="56" width="12" height="12"/></svg>
  <div class="badge">NEW</div>
  <div class="shot" role="img" aria-label="Soap bar in white and black gift boxes" style="background:linear-gradient(90deg,#ececec 40%,#1f1f1f 60%);top:105px;height:85px;width:130px;left:22px"></div>
</div>

<footer class="abs footer">
  <div class="col" style="left:67px"><h3>INFORMATIONS</h3><ul><li class="hl">Our Blog</li><li>About Our Shop</li><li>Secure Shopping</li><li>Privacy Policy</li><li>Delivery Informations</li></ul></div>
  <div class="col" style="left:273px"><h3>CUSTOMER CARE</h3><ul><li>Contact Us</li><li>Site Map</li><li>Top Sales &amp; Bestsellers</li><li>Gift Vouchers</li><li>Best Sellers</li></ul></div>
  <div class="col" style="left:498px"><h3>YOUR ACCOUNT</h3><ul><li>Order Status</li><li>My Wishlist</li><li>Delivery Address</li><li>Order History</li><li>Newsletter</li></ul></div>
  <div class="col" style="left:678px"><h3 style="letter-spacing:.3px">GET IN TOUCH</h3><ul><li>Larkspur Cosmetics Shop</li><li>Fern Lane 48, Meadow Centre</li><li>(011) 555 0148</li></ul></div>
  <div class="social"><i></i><i></i><i></i><i></i><i></i><i></i></div>
</footer>
<div class="abs base">
  <div class="c">Copyright © . All Rights Reserved</div>
  <div class="pay"><i style="background:#4a6fb0"></i><i style="background:#5b8fc9"></i><i style="background:#3b5bb0"></i><i style="background:#e08a2a"></i></div>
</div>
</body>
</html>
```